Presentation Box for dry goods meat product

We would like a box designed for presentation on a shelf. Our product is fully cooked meats (beef, pork and chicken) that has a 12- to 18-month shelf-life without refrigeration. It's not dried food, but because of the cooking process it's succulent meat in sauce, storable at room temperature.Our anchor product will be "Timber Hollow Smoke Pot."The dimensions for the box will be approximately 8" tall by 5" wide and 2.5" deep.We have an oval-shaped (horizontal) logo in Navy, Crimson and Old Gold (think Dunmore Lanterns colors).
Updates

Reason: We haven't received enough options. We want the design to say "Timber Hollow Style Smoke Pot" not "Timber Hollow Smoke Pot." Use pictures of beef brisket (not steaks), pulled pork (not pork chops) and pulled chicken (not chicken legs/thighs).

Target Market(s)

Meat-buying consumers

Industry/Entity Type

Cooking

Requirements
Must have
• Space for ingredients and nutrition information. The name of our company is Merrow Foods.
Nice to have
• Picture of Bar-B-Que beef, pork and chicken

```html
<!DOCTYPE html>
<html lang="en">
<head>
<meta charset="utf-8">
<title>Timber Hollow Smoke Pot – Box Design</title>
<link rel="stylesheet" href="https://fonts.googleapis.com/css2?family=Oswald:wght@500;600&family=Roboto+Condensed:wght@400;700&display=swap">
<style>
  :root {
    --bg: #ececec;
    --navy-deep: #0a1640;
    --navy: #13236a;
    --navy-light: #21378f;
    --gold: #d9a847;
    --crimson: #d01a1a;
    --white: #ffffff;
    --ink: #111111;
    --pale-blue: #c9d6ff;
    --meat-dark: #5a2414;
    --meat: #9a4a2c;
    --meat-light: #c4724a;
  }
  * { box-sizing: border-box; margin: 0; padding: 0; }
  html, body { width: 1200px; height: 943px; overflow: hidden; }
  body {
    background: radial-gradient(ellipse at center, #ffffff 0%, var(--bg) 75%);
    font-family: "Roboto Condensed", Arial, sans-serif;
    position: relative;
  }
  .box-dieline { position: absolute; left: 285px; top: 135px; width: 630px; height: 672px; display: flex; }

  /* Front panel */
  .front-panel {
    position: relative; width: 420px; height: 672px; overflow: hidden;
    background: linear-gradient(160deg, var(--navy-deep) 0 38%, var(--navy-light) 38% 52%, var(--navy) 52% 70%, var(--navy-deep) 70%);
  }
  .front-panel .white-strip { position: absolute; left: 0; top: 0; bottom: 0; width: 28px; background: var(--white); }
  .brand-mark { position: absolute; left: 40px; top: 38px; display: flex; align-items: center; gap: 6px; }
  .brand-mark .dot { width: 12px; height: 12px; border-radius: 50%; background: var(--gold); }
  .brand-mark .name { font-family: "Oswald", Arial, sans-serif; font-weight: 600; font-size: 18px; color: var(--white); letter-spacing: .5px; }
  .product-title {
    position: absolute; left: 62px; top: 232px; width: 340px;
    font-family: "Oswald", Arial, sans-serif; font-weight: 600; font-size: 50px; line-height: 1.12;
    color: var(--gold); letter-spacing: .3px;
  }
  .product-title .line-two { display: block; text-align: right; padding-right: 10px; }
  .title-swoosh { position: absolute; left: 170px; top: 372px; width: 220px; height: 20px; }
  .product-photo {
    position: absolute; left: 0; right: 0; bottom: 0; height: 290px;
    background: radial-gradient(ellipse at 45% 40%, var(--meat-light) 0%, var(--meat) 45%, var(--meat-dark) 100%);
    clip-path: polygon(0 18%, 100% 4%, 100% 100%, 0 100%);
  }
  .net-weight { position: absolute; right: 18px; bottom: 16px; color: var(--white); font-size: 13px; font-weight: 700; letter-spacing: .5px; }

  /* Side panel */
  .side-panel {
    position: relative; width: 210px; height: 672px; padding: 16px 14px;
    background: linear-gradient(180deg, var(--navy) 0%, var(--navy-deep) 100%);
    color: var(--white);
  }
  .nutrition-facts { background: var(--white); color: var(--ink); padding: 7px 8px; font-size: 8.5px; line-height: 1.35; }
  .nutrition-facts h2 { font-family: "Oswald", Arial, sans-serif; font-weight: 600; font-size: 18px; line-height: 1; border-bottom: 1px solid var(--ink); padding-bottom: 3px; }
  .nutrition-facts .thick { border-bottom: 5px solid var(--ink); padding-bottom: 2px; }
  .nutrition-facts .row { display: flex; justify-content: space-between; border-bottom: 1px solid var(--ink); }
  .nutrition-facts .indent { padding-left: 8px; }
  .nutrition-facts .bold { font-weight: 700; }
  .nutrition-facts .mid { border-bottom-width: 3px; }
  .nutrition-facts .footnote { font-size: 7.5px; margin-top: 3px; }
  .claims { margin-top: 18px; text-align: center; font-family: "Oswald", Arial, sans-serif; font-weight: 500; font-size: 13px; line-height: 1.25; color: var(--pale-blue); letter-spacing: .5px; }
  .fine-print { margin-top: 16px; font-size: 8.5px; line-height: 1.45; text-transform: uppercase; }
  .fine-print + .fine-print { margin-top: 12px; }
  .fine-print.address { text-transform: none; }
</style>
</head>
<body>
  <main class="box-dieline">
    <section class="front-panel">
      <div class="white-strip"></div>
      <div class="brand-mark"><span class="dot"></span><span class="name">Merrow Foods</span></div>
      <h1 class="product-title">Timber Hollow <span class="line-two">Smoke Pot</span></h1>
      <svg class="title-swoosh" viewBox="0 0 220 20" aria-hidden="true">
        <path d="M2 16 Q110 2 218 6 Q110 8 2 18 Z" fill="var(--crimson)"/>
      </svg>
      <div class="product-photo" role="img" aria-label="Photo of sliced barbecue beef brisket with glazed crust"></div>
      <div class="net-weight">NET WT 5oz</div>
    </section>

    <aside class="side-panel">
      <div class="nutrition-facts">
        <h2>Nutrition Facts</h2>
        <div>Serving Size 1 Box (142g)</div>
        <div class="thick">Servings Per Box 1</div>
        <div class="row bold"><span>Amount Per Serving</span></div>
        <div class="row mid"><span class="bold">Calories 210</span></div>
        <div class="row bold"><span></span><span>% Daily Value*</span></div>
        <div class="row"><span><b>Total Fat</b> 9g</span><span>14%</span></div>
        <div class="row indent"><span>Saturated Fat 3g</span><span>15%</span></div>
        <div class="row"><span><b>Cholesterol</b> 60mg</span><span>20%</span></div>
        <div class="row"><span><b>Sodium</b> 480mg</span><span>20%</span></div>
        <div class="row"><span><b>Total Carbohydrate</b> 12g</span><span>4%</span></div>
        <div class="row indent"><span>Dietary Fiber 0g</span><span>0%</span></div>
        <div class="row indent"><span>Sugars 9g</span></div>
        <div class="row mid"><span><b>Protein</b> 20g</span></div>
        <div class="row"><span>Vitamin A 2%</span><span>Vitamin C 0%</span></div>
        <div class="row"><span>Calcium 2%</span><span>Iron 10%</span></div>
        <p class="footnote">*Percent Daily Values are based on a 2,000 calorie diet.</p>
      </div>

      <p class="claims">GLUTEN FREE<br>MALTITOL FREE</p>

      <p class="fine-print">Ingredients: Beef brisket, tomato paste, brown sugar, vinegar, water, molasses, salt, spices, onion, garlic, smoke flavor.</p>
      <p class="fine-print">Allergen info: Contains soy. Made in a facility that also processes wheat and milk.</p>
      <p class="fine-print address">Distributed by Merrow Foods<br>410 Birchline Road<br>Fallsmere Valley<br>www.merrowfoods.example</p>
    </aside>
  </main>
</body>
</html>
```